Corvane Business Cards

Front of business card will have logo, name, address, & telephone number. Back of card will have a list of services provided - Roads, Substation Pads, Temporary Pads, Site Pads, Land Leveling, Powerline Row Cleaning, Land Clearing, Gates, Fencing, Construction Entrances, Excavation, Trenching, Underground Utilities, Directional Boring, Pile Driving. We are a construction company that uses heavy equipment like bulldozers, motor graders/blades, dump trucks, backhoes, hydro axes, & skid loaders. We build roads, pads, & install electric utility lines & waterlines underground. This logo is new. The word "Construction" can be smaller as uploaded 2 example edited logos. We will be using this card design for many employees.
Target Market(s)
Industrial Electric Powerline, Wind Turbine, Solar Panel, & Water Utility companies.
Contact Information for Business Card
Name/Position - Dwayne Halster - Owner
Address: 4875 FM 309
Harlow Creek, TX 79412
Phone number - (325) 482-5096

```html
<!DOCTYPE html>
<html lang="en">
<head>
<meta charset="UTF-8">
<title>Corvane Construction – Business Cards</title>
<link href="https://fonts.googleapis.com/css2?family=Marcellus&family=Arimo:wght@400;700&family=Open+Sans:wght@400&display=swap" rel="stylesheet">
<style>
  :root {
    --backdrop: #141414;
    --card-light: #ececea;
    --card-dark: #2b2b2c;
    --card-dark-mark: #343435;
    --maroon: #4b1a20;
    --edge: #5a1d26;
    --ink-grey: #555555;
    --rule-grey: #9a9a9a;
    --service-text: #f2f2f2;
  }
  * { box-sizing: border-box; margin: 0; padding: 0; }
  html, body {
    width: 1200px;
    height: 822px;
    overflow: hidden;
    background: var(--backdrop);
  }
  .canvas {
    position: relative;
    width: 1200px;
    height: 822px;
  }
  .card {
    position: absolute;
    top: 268px;
    width: 500px;
    height: 286px;
    border-radius: 3px;
    overflow: hidden;
  }

  /* Front */
  .card-front {
    left: 80px;
    background: var(--card-light);
  }
  .brand {
    position: absolute;
    top: 58px;
    left: 0;
    width: 100%;
    text-align: center;
    color: var(--maroon);
    font-family: "Marcellus", serif;
  }
  .brand-name {
    display: inline-flex;
    align-items: center;
    gap: 12px;
    font-size: 46px;
    letter-spacing: 3px;
    line-height: 1;
  }
  .brand-square {
    width: 16px;
    height: 16px;
    background: var(--maroon);
  }
  .brand-sub {
    margin-top: 6px;
    font-size: 22px;
    letter-spacing: 2px;
  }
  .person {
    position: absolute;
    top: 160px;
    left: 0;
    width: 100%;
    text-align: center;
  }
  .person-name {
    font-family: "Marcellus", serif;
    color: var(--maroon);
    font-size: 19px;
    letter-spacing: 3px;
  }
  .person-role {
    font-family: "Arimo", sans-serif;
    color: var(--ink-grey);
    font-size: 11px;
    margin-top: 2px;
  }
  .person-rule {
    width: 86px;
    height: 1px;
    background: var(--rule-grey);
    margin: 4px auto 0;
  }
  .contact {
    position: absolute;
    left: 34px;
    bottom: 34px;
    font-family: "Arimo", sans-serif;
    font-size: 13px;
    color: var(--ink-grey);
    white-space: nowrap;
  }
  .contact-label {
    color: var(--maroon);
    font-weight: 700;
  }

  /* Back */
  .card-back {
    left: 620px;
    background: var(--card-dark);
    border-bottom: 4px solid var(--edge);
  }
  .back-mark {
    position: absolute;
    top: 30px;
    left: 26px;
    font-family: "Marcellus", serif;
    font-size: 92px;
    letter-spacing: 4px;
    color: var(--card-dark-mark);
    line-height: 1;
  }
  .services {
    position: absolute;
    right: 24px;
    bottom: 30px;
    font-family: "Open Sans", sans-serif;
    font-size: 11.5px;
    line-height: 1.55;
    color: var(--service-text);
    white-space: nowrap;
  }
</style>
</head>
<body>
  <main class="canvas">
    <section class="card card-front" aria-label="Business card front">
      <div class="brand">
        <div class="brand-name"><span class="brand-square"></span>CORVANE</div>
        <div class="brand-sub">CONSTRUCTION</div>
      </div>
      <div class="person">
        <div class="person-name">DWAYNE HALSTER</div>
        <div class="person-role">Owner</div>
        <div class="person-rule"></div>
      </div>
      <p class="contact"><span class="contact-label">P:</span> (325) 482-5096 &nbsp;|&nbsp; 4875 FM 309 Harlow Creek, TX 79412</p>
    </section>

    <section class="card card-back" aria-label="Business card back">
      <div class="back-mark">CORVANE</div>
      <p class="services">
        Roads, Substation Pads | Temporary Pads | Site Pads,<br>
        Land Leveling | Powerline Row Cleaning | Land Clearing<br>
        Gates | Fencing, Construction Entrances | Excavation<br>
        Trenching | Underground Utilities | Directional Boring | Pile Driving.
      </p>
    </section>
  </main>
</body>
</html>
```